Need Flyer for Our Real estate Agency

Need to run General Campaign for our agency with Start of New Year as our theme ..Must have an agent's picture on the DL..
Address:
27 / 486Brindle rd, Marsden VIC 3047
Ph:03 9412 7306
email:info@kovalinrealestate.com.au
www.kovalinrealestate.com.au
Something like as attached picture..
Target Market(s)
Home Buyers
Industry/Entity Type
Real Estate Agent
Requirements
Must have
- Our Logo Colours

```html
<!DOCTYPE html>
<html lang="en">
<head>
<meta charset="utf-8">
<title>Kovalin Real Estate – DL Flyer</title>
<link rel="stylesheet" href="https://fonts.googleapis.com/css2?family=Lato:wght@300;400;700;900&display=swap">
<style>
  :root {
    --page: #e9e9eb;
    --navy-deep: #0b1c55;
    --navy: #17306f;
    --maroon: #7a1420;
    --silver: #c9cacd;
    --white: #ffffff;
    --ink-maroon: #7a1420;
  }
  * { margin: 0; padding: 0; box-sizing: border-box; }
  html, body {
    width: 1200px; height: 1198px; overflow: hidden;
    background: var(--page);
    font-family: "Lato", Arial, sans-serif;
  }
  .flyer {
    position: absolute; left: 109px; width: 968px; height: 461px;
    box-shadow: 0 6px 14px rgba(0,0,0,.28);
    overflow: hidden; color: var(--white);
  }
  .flyer--front { top: 109px; }
  .flyer--back { top: 641px; }
  .flyer__art { position: absolute; inset: 0; width: 968px; height: 461px; display: block; }

  .brand {
    position: absolute; left: 440px; right: 0; top: 92px;
    text-align: center; font-weight: 400; font-size: 38px;
    letter-spacing: 5px; text-transform: uppercase; color: var(--white);
  }
  .brand__dot {
    display: inline-block; width: 10px; height: 10px; background: var(--maroon);
    vertical-align: middle; margin-right: 14px; position: relative; top: -4px;
  }

  .headline {
    position: absolute; left: 440px; right: 0; top: 214px;
    text-align: center; font-weight: 300; font-size: 31px; line-height: 45px;
  }
  .subline {
    position: absolute; left: 440px; right: 0; top: 325px;
    text-align: center; font-weight: 400; font-size: 15px; text-transform: uppercase;
  }
  .subline strong { font-weight: 900; }

  .cta {
    position: absolute; left: 521px; top: 372px; width: 364px; height: 47px;
    background: var(--white); border-radius: 24px;
    box-shadow: 0 3px 6px rgba(0,0,0,.3);
    display: flex; align-items: center; justify-content: center; gap: 8px;
    color: var(--ink-maroon); font-weight: 900; font-size: 20px; text-transform: uppercase;
  }
  .cta__icon { width: 20px; height: 20px; }
  .cta__number { text-transform: none; }
  .cta-note {
    position: absolute; left: 440px; right: 0; top: 427px;
    text-align: center; font-weight: 400; font-size: 17px;
  }

  .contact-list {
    position: absolute; left: 577px; top: 230px; list-style: none;
  }
  .contact-list li {
    display: flex; align-items: center; gap: 14px; height: 41px;
    font-weight: 300; font-size: 19px;
  }
  .contact-list svg { width: 20px; height: 20px; flex: none; }
  .address {
    position: absolute; left: 440px; right: 0; top: 414px;
    text-align: center; font-weight: 300; font-size: 18px;
  }
</style>
</head>
<body>

<!-- Front of DL -->
<section class="flyer flyer--front">
  <svg class="flyer__art" viewBox="0 0 968 461" aria-hidden="false">
    <defs>
      <linearGradient id="navyFront" x1="0" y1="0" x2="1" y2="1">
        <stop offset="0" stop-color="#0a1a50"/>
        <stop offset="1" stop-color="#1b3674"/>
      </linearGradient>
      <linearGradient id="photoFront" x1="0" y1="0" x2="0" y2="1">
        <stop offset="0" stop-color="#b9c7dc"/>
        <stop offset=".55" stop-color="#a59d94"/>
        <stop offset=".8" stop-color="#4f6f3a"/>
        <stop offset="1" stop-color="#3f5e2e"/>
      </linearGradient>
      <clipPath id="navyClipFront"><path d="M385 0 Q520 215 418 461 H968 V0 Z"/></clipPath>
    </defs>
    <g role="img" aria-label="Photo of the agent in a blue suit in front of a large two-storey home">
      <rect width="480" height="461" fill="url(#photoFront)"/>
    </g>
    <path d="M282 0 Q480 215 392 461 H968 V0 Z" fill="var(--white)"/>
    <path d="M305 0 Q500 215 404 461 H968 V0 Z" fill="var(--silver)"/>
    <path d="M385 0 Q520 215 418 461 H968 V0 Z" fill="url(#navyFront)"/>
    <g clip-path="url(#navyClipFront)">
      <rect x="0" y="390" width="968" height="3" fill="var(--white)"/>
      <rect x="0" y="393" width="968" height="68" fill="var(--maroon)"/>
    </g>
  </svg>

  <div class="brand"><span class="brand__dot"></span>Kovalin Real Estate</div>
  <h1 class="headline">Curios to know what your<br>home is worth?</h1>
  <p class="subline">Start of new year with <strong>Ravi Dhillon</strong> and find out!</p>
  <div class="cta">
    <span>Call me now!</span>
    <svg class="cta__icon" viewBox="0 0 24 24"><circle cx="12" cy="12" r="10.5" fill="none" stroke="currentColor" stroke-width="2"/><path d="M8.3 6.8c.4-.4 1-.4 1.3 0l1.3 1.7c.3.4.2.9-.1 1.2l-.7.6c.6 1.4 1.6 2.5 3 3.1l.6-.7c.3-.3.8-.4 1.2-.1l1.7 1.3c.4.3.4.9 0 1.3l-.9.9c-.6.6-1.6.7-2.4.3-2.6-1.3-4.6-3.3-5.9-5.9-.4-.8-.3-1.8.3-2.4z" fill="currentColor"/></svg>
    <span class="cta__number">03 9412 7306</span>
  </div>
  <p class="cta-note">For Free property Appraisal</p>
</section>

<!-- Back of DL -->
<section class="flyer flyer--back">
  <svg class="flyer__art" viewBox="0 0 968 461">
    <defs>
      <linearGradient id="navyBack" x1="0" y1="0" x2="1" y2="1">
        <stop offset="0" stop-color="#0a1a50"/>
        <stop offset="1" stop-color="#1b3674"/>
      </linearGradient>
      <linearGradient id="photoBack" x1="0" y1="0" x2="0" y2="1">
        <stop offset="0" stop-color="#8fb0d6"/>
        <stop offset=".45" stop-color="#d8d2c4"/>
        <stop offset=".8" stop-color="#8a8a6c"/>
        <stop offset="1" stop-color="#5d6a3f"/>
      </linearGradient>
      <clipPath id="navyClipBack"><path d="M385 0 Q520 215 418 461 H968 V0 Z"/></clipPath>
    </defs>
    <g role="img" aria-label="Photo of a sold, home for sale sign in front of a house">
      <rect width="480" height="461" fill="url(#photoBack)"/>
    </g>
    <path d="M282 0 Q480 215 392 461 H968 V0 Z" fill="var(--white)"/>
    <path d="M305 0 Q500 215 404 461 H968 V0 Z" fill="var(--silver)"/>
    <path d="M385 0 Q520 215 418 461 H968 V0 Z" fill="url(#navyBack)"/>
    <g clip-path="url(#navyClipBack)">
      <rect x="0" y="392" width="968" height="3" fill="var(--white)"/>
      <rect x="0" y="395" width="968" height="66" fill="var(--maroon)"/>
    </g>
  </svg>

  <div class="brand"><span class="brand__dot"></span>Kovalin Real Estate</div>
  <ul class="contact-list">
    <li>
      <svg viewBox="0 0 24 24"><circle cx="12" cy="12" r="10.5" fill="none" stroke="#fff" stroke-width="1.6"/><path d="M8.3 6.8c.4-.4 1-.4 1.3 0l1.3 1.7c.3.4.2.9-.1 1.2l-.7.6c.6 1.4 1.6 2.5 3 3.1l.6-.7c.3-.3.8-.4 1.2-.1l1.7 1.3c.4.3.4.9 0 1.3l-.9.9c-.6.6-1.6.7-2.4.3-2.6-1.3-4.6-3.3-5.9-5.9-.4-.8-.3-1.8.3-2.4z" fill="#fff"/></svg>
      <span>03 9412 7306</span>
    </li>
    <li>
      <svg viewBox="0 0 24 24"><circle cx="12" cy="12" r="10.5" fill="none" stroke="#fff" stroke-width="1.6"/><rect x="6.5" y="8" width="11" height="8" rx="1" fill="#fff"/><path d="M6.8 8.5 12 12.5l5.2-4" fill="none" stroke="#17306f" stroke-width="1.2"/></svg>
      <span>info@kovalinrealestate.com.au</span>
    </li>
    <li>
      <svg viewBox="0 0 24 24" fill="none" stroke="#fff" stroke-width="1.4"><circle cx="12" cy="12" r="10.5" stroke-width="1.6"/><circle cx="12" cy="12" r="6"/><ellipse cx="12" cy="12" rx="2.6" ry="6"/><path d="M6 12h12"/></svg>
      <span>www.kovalinrealestate.com.au</span>
    </li>
  </ul>
  <p class="address">27 / 486 Brindle Rd, Marsden, Victoria, Australia 3047</p>
</section>

</body>
</html>
```